Wordpress Business Travel Blog and Discussion Board

Oh, Hello!

We are looking for a motivated designer to create a full, turnkey interactive WordPress website geared toward business travel that includes a news style blog (look at ByteHarbor.com and Wirevane.com for the style we like) that is seamlessly integrated with a robust message board (look at GateBanter.com and RoamLedger.com). Ok, so stick with us here because this is actually a pretty cool project that shouldn't be too hard, but yes, of course we have some curve balls that we are throwing your way. Sorry! :)

*On the front page*

- We would like to have a typical news style blog layout that is fun, somewhat professional, and easy to read. That's easy!

- Somewhere within first glance, we would like to have a short list of the most active discussions on our discussion board. (What's trending, or something like that). Not too bad, right?

- Overall, want to have a good amount of content, but we also do not want the visitor to feel as if he or she is having to sift through a lot of content to see what he or she wants to see. Great! We're past the beginning!

We will have traditional visual advertising on all of our pages. Please leave space as necessary :)

*On the Blog/News story pages*

Let's keep these simple - but there is a twist!

Let's say I create a blog/news post. I would like that blog/news post to also be opened as a discussion on the discussion board. For example, I write an article about Coastal Skyways and their service on a particular international flight. This will be opened as a discussion under the Coastal Skyways topic in the discussion board. Other users can also open new discussions under any topic on the discussion board, but they cannot post stories (unless permission is given) to the blog wall. We would like their posts to show up as regular discussion board posts while the news/blog posts by us show up as news/blog posts on the front page, *and* (oh yes we did!) as discussions in the discussion board. Of course, users will still be able to post comments to the news/blog post, which will also be posted in the discussion.

OK, does that make sense? Let me know if I can help make this more clear! :) Sorry!

*Wiki Pages*

Take a look at the Coastal Skyways example above. In that example, my news/blog entry automatically opens a new discussion post. Although we won't necessarily need to create a new wiki page, we would like to tag the post and the discussion to a wiki page about the topic. The wiki page can be created and edited by all users (and locked by us if necessary). BONUS! Can we tag more than one wiki page?

*Websites that inspire us*

ByteHarbor.com - concept and design
Wirevane.com - concept and design
GateBanter.com - concept
RoamLedger.com - concept
pomwhispers.com - concept

All of the sites above are great and we can only thrive with their great success. We are not aiming to be a competitor to the travel sites, but just another great option for interested visitors. Please do not simply copy what they have. What is posted above is a list of our favorite sites that we visit every day.

Our favorite font is Segoe UI, but please don't use this (or a similar font) too much! Maybe just titles would be great. You're the designer so you can make the call here.

Also, our favorite color is blue, but if you have another favorite color, go ahead and show us what you can do! (Don't use too much blue!)

*Oh, and One More Thing*

(I know, you thought we were done. We're not!)

Here's the killer - We would like to create a way for people to, say, enter the details of their next trip and be matched with someone who will also be on a portion of their trip.

For example, let's say I am flying Meridian Airways flight 109 from Los Angeles to New York JFK Airport this Friday. I am staying at the Bellcourt New York Times Square on Friday night, and I am flying back on Saturday night on Kestrel flight 290 from New York JFK airport back to Los Angeles. Another user will also be on the Kestrel flight back to Los Angeles with me and he entered that information in the website. (Note, the user has to manually enter this information). The other user and I will both be notified that there is at least one other user who will be on the same Kestrel flight as me. We will both have the option to reveal our online identity - which will in fact be released to each person as long as each person *mutually* agrees.

This can be very simple - almost like a dating site type of match but it is based on two people being in the same place at the same time (based on what they report). Also, we would like to be able to collect this information - not necessarily tied to the user's true identity. The information we would like to have is - what the user is claiming he or she is doing on the trip (i.e. staying at the Bellcourt Times Square, flying Meridian Airways), and whether or not the user agreed to reveal his or her identity - AND! whether or not the users both revealed their identity.

*Most Important*

HAVE FUN and THANK YOU!! :)

A couple of quick notes - this is a design and code project. We are most likely offering a more $(!) design and code project for the version 2.0 of this website once we get user feedback from this first round.

Also, the name of the website is Jaunta. (www.jaunta-example.com)

Good luck!

Reason: Extending as requested by a few designers. Only 3 more days to get your designs in!

Reason: All designs look great! Last chance for one or two more designers who have requested an extension. All designs that were already submitted on time will be considered with much higher priority. Thank you!

Requirements
Must have
• We need to have a high end, professional, modern, and clean design on the front page to entice readers to constantly visit and stay on our site.
Nice to have
• It would be great to give us the ability to automatically recognize users for visiting the website and/or participating and commenting. Social badges, recognition, etc. would be very cool.
Should not have
• Although this is a website around business travel, we do not necessarily want it to be business travel themed. There can be hints of the theme, but otherwise the visual look should be somewhat generic.

```html
<!DOCTYPE html>
<html lang="en">
<head>
<meta charset="utf-8">
<title>Tidewell Travels</title>
<link href="https://fonts.googleapis.com/css2?family=Oswald:wght@300;400&family=Arimo:wght@400;700&display=swap" rel="stylesheet">
<style>
:root{
  --sky:#1c78d6;
  --sky-light:#5fb0ee;
  --sea:#27b3c4;
  --sand:#f2b41e;
  --sand-deep:#e3901a;
  --bar:#e9e7e1;
  --bar-edge:#d7d4cb;
  --ink:#3d3d3d;
  --ink-soft:#555;
  --panel:#efeeef;
  --panel-line:#c9c9c9;
  --accent:#b06e4d;
  --accent-deep:#94543a;
  --accent-tip:#e59a78;
  --white:#fff;
  --navy:#2b3c5c;
}
*{margin:0;padding:0;box-sizing:border-box}
html,body{width:1063px;height:1200px;overflow:hidden}
body{position:relative;font-family:"Arimo",Arial,sans-serif;color:var(--ink)}
.scenery{position:absolute;inset:0;background:linear-gradient(180deg,var(--sky) 0%,var(--sky-light) 40%,#a8d6f2 52%,var(--sea) 58%,#6fc4c6 66%,var(--sand) 72%,var(--sand-deep) 100%)}
.condensed{font-family:"Oswald","Arial Narrow",sans-serif;font-weight:400;text-transform:uppercase;letter-spacing:-.2px;white-space:nowrap}
.top-links{position:absolute;top:4px;right:0;width:1063px;height:20px}
.top-links a{position:absolute;color:var(--white);font-size:12.5px;text-decoration:none;font-family:"Oswald","Arial Narrow",sans-serif;font-weight:300}
.brand{position:absolute;left:0;width:1063px;top:28px;text-align:center;font-family:"Oswald","Arial Narrow",sans-serif;font-weight:400;font-size:38px;color:var(--white)}
.ribbon{position:absolute;left:58px;top:118px;width:949px;height:70px}
.nav-bar{position:absolute;left:89px;top:107px;width:886px;height:70px;background:linear-gradient(#f1efea,var(--bar));box-shadow:0 3px 6px rgba(0,0,0,.25)}
.nav-bar ul{list-style:none;position:absolute;left:28px;top:24px;display:flex}
.nav-bar li{font-size:14.5px;color:var(--ink-soft);padding:0 17px;border-left:1px solid #b9b6ae;line-height:14px}
.nav-bar li:first-child{border-left:0;padding-left:0}
.search{position:absolute;left:698px;top:24px;width:173px;height:19px;background:var(--white);border:1px solid #d9d7d1;font-size:10px;color:#666;padding:3px 4px}
.search svg{position:absolute;right:5px;top:3px}
.page{position:absolute;left:101px;top:179px;width:864px;height:945px;background:rgba(233,235,238,.86)}
.hero-photo{position:absolute;left:0;top:0;width:594px;height:315px;background:linear-gradient(180deg,#9fc7e2 0%,#cfe1ea 35%,#e9e3da 70%,#d6c7b4 100%)}
.feature{position:absolute;left:594px;top:0;width:270px;height:368px}
.feature h2{position:absolute;left:19px;top:34px;font-size:23px;letter-spacing:-.6px;color:var(--white);line-height:28px}
.feature p{position:absolute;left:19px;top:67px;width:230px;font-size:12.2px;line-height:14.6px;color:var(--white);text-align:justify}
.dots{position:absolute;left:101px;top:285px;display:flex;gap:5px}
.dots i{width:14px;height:14px;border-radius:50%;background:#cf8a6a;border:1px solid #8c4d34;display:block}
.tab{position:absolute;background:var(--panel);border:1px solid var(--panel-line);border-bottom:0;color:var(--ink-soft);text-align:center}
.box{position:absolute;background:var(--panel);border:1px solid var(--panel-line)}
.topics-tab{left:105px;top:520px;width:114px;height:31px;font-size:19px;line-height:31px;z-index:2}
.topics{left:105px;top:550px;width:589px;height:520px}
.post{position:absolute;left:0;width:589px}
.post .thumb{position:absolute;left:8px;width:221px;height:97px;background:linear-gradient(180deg,#2f7cd0 0%,#8ec0e6 45%,#c77a46 62%,#a9582f 80%,#2d6fb6 100%)}
.post h3{position:absolute;left:237px;top:5px;font-size:17px;color:#474747;line-height:20px}
.post .meta{position:absolute;left:237px;top:25px;font-size:10.6px;color:#222}
.post .excerpt{position:absolute;left:237px;top:44px;width:345px;font-size:10.6px;line-height:12.8px;color:#2b2b2b;text-align:justify}
.count{position:absolute;left:455px;top:105px;width:26px;height:24px;background:#878787;color:var(--white);font-size:12px;text-align:center;line-height:24px}
.count::after{content:"";position:absolute;left:4px;bottom:-5px;border-left:5px solid #878787;border-bottom:5px solid transparent}
.more{position:absolute;left:496px;top:102px;width:81px;height:28px;border:1px solid #cfcfcf;border-radius:4px;background:linear-gradient(#f2f2f2,#dedede);font-size:11.5px;font-weight:700;color:#666;text-align:center;line-height:26px}
.divider{position:absolute;left:10px;width:572px;border-top:1px solid #c4c4c4}
.subscribe h3{position:absolute;left:709px;width:250px;top:577px;text-align:center;font-size:18px;color:#3f3f3f}
.subscribe .field{position:absolute;left:739px;top:601px;width:169px;height:21px;background:var(--white);border:1px solid #c8c8c8;border-radius:3px}
.subscribe .button{position:absolute;left:791px;top:633px;width:74px;height:22px;background:#c6c5c3;border-radius:3px;font-size:13px;text-align:center;line-height:22px;color:#3f3f3f}
.side-tab{top:680px;height:32px;font-size:14px;line-height:30px;z-index:2}
.recent-tab{left:709px;width:85px}
.tweets-tab{left:798px;width:86px}
.side-box{left:709px;top:711px;width:250px;height:359px}
.recent{position:absolute;left:8px;width:230px}
.recent .thumb{position:absolute;left:0;top:0;width:68px;height:61px;background:linear-gradient(180deg,#3c8bd6 0%,#9ac7e8 40%,#c77a46 60%,#a65a33 100%)}
.recent h4{position:absolute;left:74px;top:0;font-size:15px;color:#444;line-height:18px}
.recent p{position:absolute;left:76px;top:19px;width:150px;font-size:10.5px;line-height:13px;color:#333}
.dash{position:absolute;left:24px;width:193px;border-top:1px dashed #a9a9a9}
.see-all{position:absolute;right:10px;top:347px;font-size:10.5px;color:#222;text-decoration:underline}
.footer{position:absolute;left:101px;top:1086px;width:864px;height:38px;background:linear-gradient(#dedbd4,#cfcbc2)}
.footer a{position:absolute;top:12px;font-size:11px;color:#6b6b6b;text-decoration:none}
.follow{position:absolute;left:623px;top:12px;font-size:11px;color:#555}
.social{position:absolute;top:5px;width:27px;height:27px;border-radius:50%;background:#272727}
.copyright{position:absolute;right:106px;top:1132px;font-size:10.5px;color:var(--navy)}
</style>
</head>
<body>
<div class="scenery" role="img" aria-label="Tropical beach backdrop with palm fronds, blue sky with clouds, turquoise sea and golden sand"></div>

<nav class="top-links">
  <a style="left:780px">SIGNIN</a>
  <a style="left:831px">REGISTER</a>
  <a style="left:897px">HELP</a>
  <a style="left:945px">FAQ</a>
</nav>
<svg style="position:absolute;left:789px;top:0" width="10" height="6"><path d="M0 0h10L5 6z" fill="#fff"/></svg>

<div class="brand">Tidewell Travels</div>

<svg class="ribbon" viewBox="0 0 949 70" width="949" height="70">
  <path d="M0 0h40v70H0l12-35z" fill="#dedbd2"/>
  <path d="M949 0h-40v70h40l-12-35z" fill="#dedbd2"/>
</svg>
<header class="nav-bar">
  <ul class="condensed">
    <li>Home</li><li>About</li><li>Blog</li><li>Forums</li><li>Services</li><li>Cities</li><li>FAQ</li><li>Testimonials</li><li>Contact</li>
  </ul>
  <div class="search">Search
    <svg width="13" height="13" viewBox="0 0 13 13"><circle cx="5" cy="5" r="4" fill="none" stroke="#555" stroke-width="1.4"/><path d="M8 8l4 4" stroke="#555" stroke-width="1.6"/></svg>
  </div>
</header>

<main class="page">
  <div class="hero-photo" role="img" aria-label="Family of three holding hands and playing in the surf on a sunny beach"></div>
  <aside class="feature">
    <svg width="270" height="368" viewBox="0 0 270 368" style="position:absolute;left:0;top:0">
      <defs><linearGradient id="featureFill" x1="0" y1="0" x2="0" y2="1"><stop offset="0" stop-color="#b5735a"/><stop offset="1" stop-color="#8f4f39"/></linearGradient></defs>
      <path d="M0 0h270v315L135 368 0 315z" fill="#e7a382"/>
      <path d="M0 0h270v305L135 358 0 305z" fill="url(#featureFill)"/>
    </svg>
    <h2 class="condensed">Things to do in Europe</h2>
    <p>Lorem ipsum dolor sit amet, consectetur adipiscing elit. Sed blandit massa vel mauris sollicitudin dignissim. Phasellus ultrices tellus eget ipsum ornare molestie scelerisque eros dignissim. Phasellus fringilla hendrerit lectus nec vehicula. Pellentesque habitant morbi tristique senectus et netus et malesuada fames ac turpis egestas. In faucibus, risus eu volutpat pellentesque, massa felis feugiat velit, nec mattis felis elit a eros.</p>
    <div class="dots"><i></i><i></i><i></i><i></i></div>
  </aside>
</main>

<div class="tab topics-tab condensed">Latest Topics</div>
<section class="box topics">
  <article class="post" style="top:31px">
    <div class="thumb" role="img" aria-label="Terracotta resort hotel beside a pool under blue sky"></div>
    <h3 class="condensed">Ancient Rome - Visit Today</h3>
    <div class="meta">By Admin on July 14, 2011 in Adipisicing</div>
    <p class="excerpt">Lorem ipsum dolor sit amet, consectetur adipiscing elit. Sed blandit massa vel mauris sollicitudin dignissim. Phasellus ultrices tellus eget ipsum ornare molestie scelerisque eros dignissim. Phasellus fringilla hendrerit lectus nec vehicula. Pellentesque habitant morbi tristique senectus et netus et malesuada fames ac</p>
    <div class="count">3</div><div class="more">Read more</div>
  </article>
  <div class="divider" style="top:170px"></div>
  <article class="post" style="top:191px">
    <div class="thumb" role="img" aria-label="Terracotta resort hotel beside a pool under blue sky"></div>
    <h3 class="condensed">Ancient Rome - Visit Today</h3>
    <div class="meta">By Admin on July 14, 2011 in Adipisicing</div>
    <p class="excerpt">Lorem ipsum dolor sit amet, consectetur adipiscing elit. Sed blandit massa vel mauris sollicitudin dignissim. Phasellus ultrices tellus eget ipsum ornare molestie scelerisque eros dignissim. Phasellus fringilla hendrerit lectus nec vehicula. Pellentesque habitant morbi tristique senectus et netus et malesuada fames ac</p>
    <div class="count">3</div><div class="more">Read more</div>
  </article>
  <div class="divider" style="top:336px"></div>
  <article class="post" style="top:356px">
    <div class="thumb" role="img" aria-label="Terracotta resort hotel beside a pool under blue sky"></div>
    <h3 class="condensed">Ancient Rome - Visit Today</h3>
    <div class="meta">By Admin on July 14, 2011 in Adipisicing</div>
    <p class="excerpt">Lorem ipsum dolor sit amet, consectetur adipiscing elit. Sed blandit massa vel mauris sollicitudin dignissim. Phasellus ultrices tellus eget ipsum ornare molestie scelerisque eros dignissim. Phasellus fringilla hendrerit lectus nec vehicula. Pellentesque habitant morbi tristique senectus et netus et malesuada fames ac</p>
    <div class="count">3</div><div class="more">Read more</div>
  </article>
</section>

<section class="subscribe">
  <h3 class="condensed">Subscribe for Newletter</h3>
  <div class="field"></div>
  <div class="button condensed">Subscribe</div>
</section>

<div class="tab side-tab recent-tab condensed">Recent Posts</div>
<div class="tab side-tab tweets-tab condensed">Latest Tweets</div>
<section class="box side-box">
  <div class="recent" style="top:18px">
    <div class="thumb" role="img" aria-label="Terracotta resort hotel under blue sky"></div>
    <h4 class="condensed">Things to do in Europe</h4>
    <p>Lorem ipsum dolor sit amet conse...</p>
  </div>
  <div class="dash" style="top:90px"></div>
  <div class="recent" style="top:101px">
    <div class="thumb" role="img" aria-label="Terracotta resort hotel under blue sky"></div>
    <h4 class="condensed">Visit Rome</h4>
    <p>Lorem ipsum dolor sit amet conse...</p>
  </div>
  <div class="dash" style="top:173px"></div>
  <div class="recent" style="top:187px">
    <div class="thumb" role="img" aria-label="Terracotta resort hotel under blue sky"></div>
    <h4 class="condensed">Visit Rome</h4>
    <p>Lorem ipsum dolor sit amet conse...</p>
  </div>
  <div class="dash" style="top:263px"></div>
  <div class="recent" style="top:279px">
    <div class="thumb" role="img" aria-label="Terracotta resort hotel under blue sky"></div>
    <h4 class="condensed">Visit Rome</h4>
    <p style="top:15px">Lorem ipsum dolor sit amet conse...</p>
  </div>
  <a class="see-all">See All</a>
</section>

<footer class="footer">
  <a style="left:20px">Home</a>
  <a style="left:78px">About Us</a>
  <a style="left:145px">Blog</a>
  <a style="left:193px">Forums</a>
  <a style="left:262px">Services</a>
  <a style="left:332px">Cities</a>
  <a style="left:385px">Testimonials</a>
  <a style="left:470px">Contact Us</a>
  <span class="follow">Follow us on</span>
  <span class="social" style="left:699px" aria-label="Social profile"></span>
  <span class="social" style="left:734px" aria-label="Feed"></span>
  <span class="social" style="left:768px" aria-label="Social profile"></span>
  <span class="social" style="left:804px" aria-label="Social profile"></span>
</footer>
<div class="copyright">COPYRIGHT @ TIDEWELLTRAVELS.COM</div>
</body>
</html>
```